Letter design, envelope design, and more

Hello, we the Tavrin Gmbh are looking for our shop. Letter C5. Design does not have to be like a business card, so it can have straight lines. Only the color is important. The logo is the text under TaVRin omit.It should not be playful but Profesionel

Font styles to use
Sans Serif

Colors
0555a3
3176b5
85abd2
85cae6
34a7d8
0792cd
cee9f5
cfdfed
000000

Requirements
Must have
• Color like business card, Please, with the text under TaVRin, Correct address Lindmattstr. 4 Zip code 9517 Goldach, as well as Couvert Without addressing only design and logo with TaVrn
Nice to have
• more writing articles
Should not have
• Not too colored, Text under TaVRin, bright colors

```html
<!DOCTYPE html>
<html lang="en">
<head>
<meta charset="utf-8">
<title>Tavrin Gmbh – Letterhead and Envelopes</title>
<link href="https://fonts.googleapis.com/css2?family=Lato:ital,wght@0,400;0,700;1,400&family=Yellowtail&display=swap" rel="stylesheet">
<style>
  :root {
    --bg: #e1e2e4;
    --paper: #ffffff;
    --brand-blue: #0555a3;
    --mid-blue: #3176b5;
    --soft-blue: #85abd2;
    --text: #4a4a4a;
    --ink: #222222;
    --edge: #c9c9cc;
  }
  * { box-sizing: border-box; margin: 0; padding: 0; }
  html, body { width: 1200px; height: 641px; overflow: hidden; }
  body {
    position: relative;
    background: var(--bg);
    font-family: "Lato", sans-serif;
    color: var(--text);
  }

  /* ---------- shared ---------- */
  .brand {
    position: absolute;
    display: flex;
    align-items: center;
    gap: 6px;
    color: var(--brand-blue);
    font-family: "Lato", sans-serif;
    font-weight: 700;
    letter-spacing: 0.5px;
  }
  .brand__mark { background: var(--brand-blue); }
  .tricolor-bar {
    position: absolute;
    left: 0; right: 0; bottom: 0;
    height: 4px;
    display: flex;
  }
  .tricolor-bar span { flex: 1; }
  .tricolor-bar span:nth-child(1) { background: var(--brand-blue); }
  .tricolor-bar span:nth-child(2) { background: var(--mid-blue); }
  .tricolor-bar span:nth-child(3) { background: var(--soft-blue); }
  .icon { width: 7px; height: 7px; flex: none; color: var(--brand-blue); }

  /* ---------- letterhead ---------- */
  .letterhead {
    position: absolute;
    left: 70px; top: 69px;
    width: 364px; height: 512px;
    background: var(--paper);
    border: 1px solid var(--edge);
  }
  .letterhead .brand { left: 21px; top: 16px; font-size: 21px; }
  .letterhead .brand__mark { width: 24px; height: 24px; }
  .contact {
    position: absolute;
    left: 278px; top: 15px;
    padding-left: 5px;
    border-left: 1px solid var(--edge);
    font-size: 7px;
    color: var(--ink);
    line-height: 11px;
  }
  .contact li { list-style: none; display: flex; align-items: center; gap: 3px; }
  .letter-body {
    position: absolute;
    left: 20px; top: 86px;
    width: 328px;
  }
  .letter-body p {
    font-size: 6.6px;
    line-height: 11.2px;
    color: var(--text);
    margin-bottom: 7px;
  }
  .letter-body .salutation {
    font-size: 10px;
    line-height: 14px;
    font-weight: 700;
    color: var(--brand-blue);
    margin-bottom: 3px;
  }
  .closing {
    position: absolute;
    left: 20px; top: 396px;
    font-size: 11.5px;
    color: var(--ink);
  }
  .signature {
    position: absolute;
    left: 21px; top: 410px;
    font-family: "Yellowtail", cursive;
    font-size: 19px;
    color: var(--brand-blue);
  }
  .letter-footer {
    position: absolute;
    left: 0; right: 0; top: 493px;
    display: flex; justify-content: center; align-items: center; gap: 3px;
    font-size: 7px;
    color: var(--ink);
  }
  .letter-footer .icon { color: var(--ink); }

  /* ---------- envelopes ---------- */
  .envelope {
    position: absolute;
    width: 540px; height: 242px;
    background: var(--paper);
    border: 1px solid var(--edge);
    overflow: hidden;
  }
  .envelope__flap { position: absolute; left: 0; top: 0; width: 100%; height: 100px; }
  .envelope--back-dark { left: 594px; top: 102px; }
  .envelope--back-light { left: 554px; top: 206px; }
  .envelope--front { left: 464px; top: 314px; }
  .flap-fill { fill: var(--brand-blue); }
  .flap-line { fill: none; stroke: var(--edge); stroke-width: 1; }

  .flap-brand {
    position: absolute;
    left: 0; right: 0; top: 26px;
    justify-content: center;
    font-size: 22px;
  }
  .envelope--back-dark .flap-brand { color: var(--paper); }
  .envelope--back-dark .flap-brand .brand__mark { background: var(--paper); }
  .flap-brand .brand__mark { width: 22px; height: 22px; }

  .envelope--front .brand { left: 16px; top: 11px; font-size: 22px; }
  .envelope--front .brand__mark { width: 26px; height: 26px; }
  .return-address {
    position: absolute;
    left: 16px; top: 63px;
    display: flex; align-items: center; gap: 4px;
    font-size: 9.5px;
    color: var(--ink);
  }
  .return-address .icon { width: 9px; height: 9px; }
  .envelope-web {
    position: absolute;
    left: 0; right: 0; top: 222px;
    text-align: center;
    font-size: 9.5px;
    letter-spacing: 2px;
    color: var(--ink);
  }
  .envelope-web em { font-style: normal; color: var(--mid-blue); }
</style>
</head>
<body>

  <!-- Letterhead -->
  <section class="letterhead">
    <div class="brand"><span class="brand__mark"></span>TAVRIN</div>
    <ul class="contact">
      <li>
        <svg class="icon" viewBox="0 0 10 10"><circle cx="5" cy="5" r="4.3" fill="none" stroke="currentColor" stroke-width="1"/><path d="M3.3 2.8 L4.3 3.8 L3.8 4.4 Q4.5 5.6 5.6 6.2 L6.2 5.7 L7.2 6.7 L6.5 7.4 Q3.5 6.6 2.6 3.5 Z" fill="currentColor"/></svg>
        +41 71 402 36 18
      </li>
      <li>
        <svg class="icon" viewBox="0 0 10 10"><rect x="1" y="2.5" width="8" height="5.5" fill="currentColor"/><path d="M1 2.5 L5 6 L9 2.5" fill="none" stroke="#fff" stroke-width="0.8"/></svg>
        info@tavrin.ch
      </li>
      <li>
        <svg class="icon" viewBox="0 0 10 10"><circle cx="5" cy="5" r="4" fill="none" stroke="currentColor" stroke-width="0.9"/><ellipse cx="5" cy="5" rx="1.8" ry="4" fill="none" stroke="currentColor" stroke-width="0.7"/><path d="M1 5 H9" stroke="currentColor" stroke-width="0.7"/></svg>
        www.tavrin.ch
      </li>
    </ul>

    <div class="letter-body">
      <p class="salutation">Dear Mr. Lorem,</p>
      <p>Lorem ipsum dolor sit amet, consectetuer adipiscing elit, sed diam nonummy nibh euismod tincidunt ut laoreet dolore magna aliquam erat volutpat. Ut wisi enim ad minim veniam, quis nostrud exerci tation ullamcorper suscipit lobortis nisl ut aliquip ex ea commodo consequat. Duis autem vel eum iriure dolor in hendiusto odio dignissim qui blandit praesent luptatum zzril delenit.facilisi.</p>
      <p>Lorem ipsum dolor sit amet, consectetuer adipiscing elit, sed diam nonummy nibh euismod tincidunt ut laoreet dolore magna aliquam erat volutpat. Ut wisi enim ad minim veniam, quis nostrud exerci tation ullamcorper suscipit lobortis nisl ut aliquip ex ea commodo consequat.</p>
      <p>Lorem ipsum dolor sit amet, consectetuer adipiscing elit, sed diam nonummy nibh euismod tincidunt ut laoreet dolore magna aliquam erat volutpat. Ut wisi enim ad minim veniam, quis nostrud exerci tation ullamcorper suscipit lobortis nisl ut aliquip ex ea commodo consequat. Duis autem vel eum iriure dolor in hendiusto odio dignissim qui blandit praesent luptatum zzril delenit.facilisi.</p>
      <p>Lorem ipsum dolor sit amet, consectetuer adipiscing elit, sed diam nonummy nibh euismod tincidunt ut laoreet dolore magna aliquam erat volutpat. Ut wisi enim ad minim veniam, quis nostrud exerci tation ullamcorper suscipit lobortis nisl ut aliquip ex ea commodo consequat.</p>
      <p>Lorem ipsum dolor sit amet, consectetuer adipiscing elit, sed diam nonummy nibh euismod tincidunt ut laoreet dolore magna aliquam erat volutpat. Ut wisi enim ad minim veniam, quis nostrud exerci tation ullamcorper suscipit lobortis nisl ut aliquip ex ea commodo consequat. Duis autem vel eum iriure dolor in hendiusto odio dignissim qui blandit praesent luptatum zzril delenit.facilisi.</p>
      <p>Lorem ipsum dolor sit amet, consectetuer adipiscing elit, sed diam nonummy nibh euismod tincidunt ut laoreet dolore magna aliquam erat volutpat. Ut wisi enim ad minim veniam, quis nostrud exerci tation ullamcorper suscipit lobortis nisl ut aliquip ex ea commodo consequat.</p>
    </div>

    <p class="closing">Sincerely Your,</p>
    <p class="signature">Your Name</p>

    <p class="letter-footer">
      <svg class="icon" viewBox="0 0 10 10"><circle cx="5" cy="5" r="4.3" fill="none" stroke="currentColor" stroke-width="0.8"/><path d="M5 2.3 A1.8 1.8 0 0 1 6.8 4.1 Q6.8 5.3 5 7.6 Q3.2 5.3 3.2 4.1 A1.8 1.8 0 0 1 5 2.3Z" fill="currentColor"/></svg>
      Lindmattstr. 4, Zip code 9517 Goldach
    </p>
    <div class="tricolor-bar"><span></span><span></span><span></span></div>
  </section>

  <!-- Envelope back, dark flap -->
  <section class="envelope envelope--back-dark">
    <svg class="envelope__flap" viewBox="0 0 540 100" preserveAspectRatio="none">
      <path class="flap-fill" d="M0 0 H540 C533 22 528 46 505 53 L300 92 Q270 98 240 92 L35 53 C12 46 7 22 0 0 Z"/>
    </svg>
    <div class="brand flap-brand"><span class="brand__mark"></span>TAVRIN</div>
  </section>

  <!-- Envelope back, light flap -->
  <section class="envelope envelope--back-light">
    <svg class="envelope__flap" viewBox="0 0 540 100" preserveAspectRatio="none">
      <path class="flap-line" d="M0 0 C7 22 12 46 35 53 L240 92 Q270 98 300 92 L505 53 C528 46 533 22 540 0"/>
    </svg>
    <div class="brand flap-brand"><span class="brand__mark"></span>TAVRIN</div>
  </section>

  <!-- Envelope front -->
  <section class="envelope envelope--front">
    <div class="brand"><span class="brand__mark"></span>TAVRIN</div>
    <p class="return-address">
      <svg class="icon" viewBox="0 0 10 10"><circle cx="5" cy="5" r="4.3" fill="none" stroke="currentColor" stroke-width="0.8"/><path d="M5 2.3 A1.8 1.8 0 0 1 6.8 4.1 Q6.8 5.3 5 7.6 Q3.2 5.3 3.2 4.1 A1.8 1.8 0 0 1 5 2.3Z" fill="currentColor"/></svg>
      Lindmattstr. 4, Zip code 9517 Goldach
    </p>
    <p class="envelope-web">www.<em>tavrin</em>.ch</p>
    <div class="tricolor-bar"><span></span><span></span><span></span></div>
  </section>

</body>
</html>
```